Business Card Design Project : Ridgeline Press

In preparation for market launch, Tamarind's Ridgeline Press require the development of a business card. Ridgeline Press is a Community online publishing web portal. We provide the the city of Whistler located in B.C. (Canada) business directories, News, Classified ads, News, Events and blogs etc.

The main focus of the brand is to help local businesses to corporate with their online advertisement and marketing. Meeting our clients face to face is a must (B2B).

Target Market(s)

The target market is B2B customers. Business Owners to Marketing, advertising Managers

Industry/Entity Type

Business

Requirements
Must have
• - The business card will be two sided.
the BACK side will have our logo which consist of (icon, url,slogan) submited. The logo will be middle and centred.

The FRONT side should have company details:

Company Legal Name: TAMARIND RIDGELINE MEDIA

Owen Farsk
Director of Sales & Marketing

www.tamarindridgeline.biz
owen@tamarindridgeline.biz

Phone: 604 317 8842
#2714 - 582 E. Halvern St.
Vancouver, B.C. V7K2R4 Canada
Nice to have
• - For the "FRONT" side of our business card. You can separate or re-arrange with our logo components (icon, logo,slogan). It does not have to be together.

Also our company legal name is rather long so arrange or organize the name in a way to make it shorter. Your experience and creativity will have to come in play.
Should not have
• should not have other colors beside logo color and black text (2 colors). Also nothing Three dimensional

```html
<!DOCTYPE html>
<html lang="en">
<head>
<meta charset="utf-8">
<title>Tamarind Ridgeline Media — Business Card</title>
<link rel="stylesheet" href="https://fonts.googleapis.com/css2?family=PT+Sans:wght@400;700&display=swap">
<style>
  :root {
    --brand-blue: #2a7cc4;
    --ink: #111111;
    --strip: #0b0b0b;
    --paper: #ffffff;
    --backdrop: #ebe8e3;
  }
  * { margin: 0; padding: 0; box-sizing: border-box; }
  html, body { width: 1200px; height: 900px; overflow: hidden; }
  body {
    background: var(--backdrop);
    font-family: "PT Sans", "Myriad Pro", Arial, sans-serif;
    color: var(--ink);
    position: relative;
  }
  .card {
    position: absolute;
    background: var(--paper);
    overflow: hidden;
  }
  .card--front { left: 56px; top: 58px; width: 592px; height: 382px; }
  .card--back  { left: 472px; top: 466px; width: 588px; height: 382px; }

  .side-strip {
    position: absolute;
    top: 0; right: 0; bottom: 0;
    background: var(--strip);
  }
  .card--front .side-strip { width: 63px; }
  .card--back .side-strip { width: 65px; }
  .side-strip svg { position: absolute; left: 0; top: 0; }

  .strip-url {
    position: absolute;
    left: 50%;
    white-space: nowrap;
    color: var(--brand-blue);
    font-size: 14px;
    letter-spacing: 0.3px;
    transform: translate(-50%, -50%) rotate(-90deg);
  }
  .card--front .strip-url { top: 254px; }
  .card--back .strip-url { top: 175px; }

  .wordmark {
    position: absolute;
    text-align: center;
  }
  .wordmark__name {
    font-weight: 700;
    color: var(--ink);
    letter-spacing: -0.2px;
    white-space: nowrap;
  }
  .wordmark__slogan {
    color: var(--brand-blue);
    white-space: nowrap;
  }
  .card--front .wordmark { left: 0; width: 529px; top: 114px; }
  .card--front .wordmark__name { font-size: 19.5px; line-height: 26px; }
  .card--front .wordmark__slogan { font-size: 17px; line-height: 27px; }
  .card--back .wordmark { left: 0; width: 523px; top: 176px; }
  .card--back .wordmark__name { font-size: 23px; line-height: 30px; }
  .card--back .wordmark__slogan { font-size: 19.5px; line-height: 31px; }

  .person { position: absolute; left: 48px; top: 198px; }
  .person__name {
    color: var(--brand-blue);
    font-weight: 700;
    font-size: 18px;
    line-height: 24px;
  }
  .person__title { font-weight: 700; font-size: 14px; line-height: 22px; }

  .contact-list {
    position: absolute;
    left: 44px; top: 260px;
    list-style: none;
    font-size: 14.5px;
    line-height: 21px;
  }
  .contact-list li { display: flex; align-items: flex-start; margin-bottom: 4px; }
  .contact-list .icon { width: 14px; height: 14px; margin: 3px 8px 0 0; flex: none; fill: var(--brand-blue); }
</style>
</head>
<body>

<section class="card card--front" aria-label="Card front">
  <div class="wordmark">
    <p class="wordmark__name">TAMARIND RIDGELINE MEDIA</p>
    <p class="wordmark__slogan">Your information gateway</p>
  </div>

  <div class="person">
    <p class="person__name">OWEN FARSK</p>
    <p class="person__title">Director of Sales &amp; Marketing</p>
  </div>

  <ul class="contact-list">
    <li>
      <svg class="icon" viewBox="0 0 14 14" aria-hidden="true"><path d="M7 1 L13 7 H11 V13 H8.5 V9 H5.5 V13 H3 V7 H1 Z"/></svg>
      <span>#2714 - 582 E. Halvern St.<br>Vancouver, B.C. V7K2R4 Canada</span>
    </li>
    <li>
      <svg class="icon" viewBox="0 0 14 14" aria-hidden="true"><path d="M3 1 L5.5 1 L6.5 4.5 L5 5.8 C5.8 7.6 6.6 8.6 8.2 9.2 L9.5 7.7 L13 8.7 L13 11.2 C13 12.3 12 13 11 13 C5.5 12.5 1.5 8.5 1 3 C1 2 2 1 3 1 Z"/></svg>
      <span>604 317 8842</span>
    </li>
    <li>
      <svg class="icon" viewBox="0 0 14 14" aria-hidden="true"><path d="M1 3.5 H13 V11 H1 Z M1.5 4 L7 8 L12.5 4" stroke="#fff" stroke-width="0.9"/></svg>
      <span>owen@tamarindridgeline.biz</span>
    </li>
  </ul>

  <div class="side-strip">
    <svg width="63" height="382" viewBox="0 0 63 382" aria-hidden="true">
      <polygon points="3,82 63,44 63,118" fill="#fff"/>
      <polygon points="15,82 58,55 58,109" fill="var(--brand-blue)"/>
    </svg>
    <span class="strip-url">www.tamarindridgeline.biz</span>
  </div>
</section>

<section class="card card--back" aria-label="Card back">
  <div class="wordmark">
    <p class="wordmark__name">TAMARIND RIDGELINE MEDIA</p>
    <p class="wordmark__slogan">Your information gateway</p>
  </div>

  <div class="side-strip">
    <svg width="65" height="382" viewBox="0 0 65 382" aria-hidden="true">
      <polygon points="2,310 2,354 40,332" fill="var(--brand-blue)"/>
    </svg>
    <span class="strip-url">www.tamarindridgeline.biz</span>
  </div>
</section>

</body>
</html>
```